Retail Jewelry Business Card Design Project

We are in need of a new business card design for a retail jewelry store. This store is in the business of fine jewelry including but not specific to bridal jewelry, diamonds, designer jewelry and watches.

This store has been in business for 20 years but continues to strive for a modern professional appeal. The main colors use for this business are a royal blue, white and silver.

Target Market(s)

Target market is ages 18-50

Industry/Entity Type

Jewelry

Requirements
Must have
• Sales Person Name
Sales Person Email Address

Store Address
Store Phone
Website

Standard business card size. No odd shapes or sizes.
Nice to have
• Overall modern feel for card.

We have thought that a design with a nice feature of the logo on the back of the card would be nice but open to ideas.
Should not have
• No specific images of jewelry should be used.

```html
<!DOCTYPE html>
<html lang="en">
<head>
<meta charset="UTF-8">
<title>Ellis Marlow Fine Jewelry – Business Card</title>
<link rel="stylesheet" href="https://fonts.googleapis.com/css2?family=Cinzel:wght@500&family=Arimo:wght@400&display=swap">
<style>
  :root {
    --royal-blue: #3326b0;
    --royal-blue-deep: #241a8c;
    --royal-blue-shade: #2a1f9c;
    --card-white: #ffffff;
    --paper-grey: #ececf0;
    --backdrop: #e4e4e8;
    --text-blue: #3a30b4;
    --brand-font: "Cinzel", serif;
    --body-font: "Arimo", sans-serif;
  }
  * { margin: 0; padding: 0; box-sizing: border-box; }
  html, body {
    width: 1200px;
    height: 1000px;
    overflow: hidden;
    background: var(--backdrop);
  }
  .sheet {
    width: 1200px;
    height: 1000px;
    display: flex;
    flex-direction: column;
    align-items: center;
    justify-content: center;
    gap: 60px;
  }
  .card {
    position: relative;
    width: 660px;
    height: 377px;
    overflow: hidden;
    box-shadow: 0 6px 20px rgba(0, 0, 0, 0.18);
  }
  .card--front {
    background: radial-gradient(ellipse at 70% 40%, var(--royal-blue) 0%, var(--royal-blue-deep) 100%);
  }
  .card--back {
    background: linear-gradient(135deg, var(--card-white) 0%, var(--card-white) 55%, var(--paper-grey) 100%);
  }
  .brand-decor {
    position: absolute;
    left: 0;
    right: 0;
    bottom: 40px;
    text-align: center;
    font-family: var(--brand-font);
    font-weight: 500;
    font-size: 92px;
    line-height: 1;
    letter-spacing: 2px;
    white-space: nowrap;
  }
  .card--front .brand-decor { color: var(--royal-blue-shade); }
  .card--back .brand-decor { color: #e2e2ea; }
  .brand-name {
    position: absolute;
    left: 0;
    right: 0;
    top: 118px;
    text-align: center;
    font-family: var(--brand-font);
    font-weight: 500;
    font-size: 38px;
    line-height: 1.25;
    letter-spacing: 2px;
    color: var(--card-white);
  }
  .contact {
    position: absolute;
    top: 44px;
    font-family: var(--body-font);
    font-size: 15px;
    line-height: 2;
    color: var(--text-blue);
  }
  .contact--person { left: 44px; }
  .contact--store { right: 44px; text-align: right; }
</style>
</head>
<body>
  <main class="sheet">
    <section class="card card--front" aria-label="Card front">
      <div class="brand-decor" aria-hidden="true">ELLIS MARLOW</div>
      <h1 class="brand-name">Ellis Marlow<br>Fine Jewelry</h1>
    </section>

    <section class="card card--back" aria-label="Card back">
      <div class="brand-decor" aria-hidden="true">ELLIS MARLOW</div>
      <address class="contact contact--person">
        Ellis Marlow Hartwell<br>
        ellis@ellismarlowjewelry.com<br>
        0421 555 017
      </address>
      <address class="contact contact--store">
        2280 Beacon Street<br>
        Harbor Point, FL 32099<br>
        www.ellismarlowjewelry.com
      </address>
    </section>
  </main>
</body>
</html>
```